Premium Relish Company Needs Postcard size Shelf talker

Business name: Corbin & Jules Velvet Foods
www.corbinandjules.com.au
Product/service/brand name:
Corbin & Jules Velvet Foods. We produce the MOST delicious premium relishes in Australia and they retail in all premium deli’s, butchers, and high end supermarkets in NSW and VIC. Please see our website for further details: www.corbinandjules.com.au
Key Objective:
Design a Post card size shelf talker. These are small signs that attach to a retail shelf ledge. Shelf Talkers are an effective way to attract and communicate with customer's in-store as they are wandering the aisles. OUR key objective is to attract EVERY single potential customer to the relish and make them buy.
Marketing objectives:
Build Brand awareness, Increase sales by creating enough curiosity for a customer to purchase the product immediately without trying it. We want something that will catch the eye and increase their interest until picking up the product off the shelf and putting it in their basket seems the most logical and sensible option to them, as opposed to them feeling they are involved in a great risk.
Our Image:
We like humour and our two phrases "Relish just got saucy" & "Makes everything better. - EVERYTHING!" reflect this. We like to appeal to their happier side when they purchase our product.
We don't want busy imagery.
Please avoid the brash colours and imagery associated with take away food. This is premium cuisine, with a modern urban angle – but not up itself. It is the perfect accompaniment to a fantastic quality BBQ for average Australian and the perfect condiment to always keep in the fridge as it is the only condiment on the market that is FULL of REAL flavour.
Key Concepts:
FUNNY, URBAN, RELEVANT
FUNNY – Chaotic Adult fun. A strong sense of the child within.
NOT CHILDLIKE
URBAN – Stay away from the conservative “country image” that most of our competitors use. We don’t want to look like we were made out on a farm somewhere.
RELEVANT – THIS IS SOMETHING EVERYONE WILL WANT TO EAT!
It is relevant to everyone and will make everything they eat it with better. Everything.
Target Audience:
Our target audience is ANYONE who loves premium quality food and is willing to pay a little bit more for a great tasting product as opposed to settling for a cheaper relish that is below average, processed and filled with additives and nasties. Our current demographic is middle-class, comfortable income, mainly Anglo-Saxon Australians - age range is quite broad from young up to professionals to comfortably set retirees.
Non Negotiable Elements of the design: The Logo
Size: Postcard - PORTRAIT ORIENTATION
File format: Happy for you to suggest which format is best.
Stock : 350gsm paper
Colours: Dominant colour must be a “Roma Tomato” Red, however keep colours down to Maximum 4
Design:
Double sided .
Front will have writing as follows with long logo incorporated as well:
CORBIN & JULES (LOGO)
Relish just got saucy (this should fit right under the logo )
• 100% Natural
• Luscious Full Flavour
• Award Winning
• Gluten Free
• Vegan Friendly
• Modern Australian Taste
.........with echoes of tradition.
Makes everything better. Everything!
Back will have burger image with short logo above it
Updates
SORRY! Forgot to mention that design layout needs to be PORTRAIT. Thanks
Reason: I have been away and need a bit more time to consider designs.

```html
<!DOCTYPE html>
<html lang="en">
<head>
<meta charset="utf-8">
<title>Corbin &amp; Jules – Shelf Talker</title>
<link href="https://fonts.googleapis.com/css2?family=Montserrat:wght@800;900&family=Open+Sans:wght@400;600;700&display=swap" rel="stylesheet">
<style>
  :root {
    --roma-red: #c81d25;
    --deep-red: #7a0f12;
    --shadow-red: rgba(70, 6, 8, 0.72);
    --gold: #e8b83a;
    --gold-dark: #b98a1e;
    --orange: #eda631;
    --sky-blue: #2f86c4;
    --white: #ffffff;
    --backdrop: #eeeeee;
  }
  * { margin: 0; padding: 0; box-sizing: border-box; }
  html, body { width: 1200px; height: 1000px; overflow: hidden; }
  body { background: var(--backdrop); font-family: "Open Sans", sans-serif; position: relative; }

  .shelf-talker {
    position: absolute; left: 242px; top: 38px; width: 718px; height: 925px;
    overflow: hidden; color: var(--white);
  }
  .backdrop-burst {
    position: absolute; inset: 0;
    background: radial-gradient(circle at 50% 42%, #d6212a 0%, var(--roma-red) 35%, #9c1418 75%, var(--deep-red) 100%);
  }
  .abs { position: absolute; }

  .brand-name {
    left: 0; width: 100%; top: 40px; text-align: center;
    font-size: 78px; font-weight: 700; line-height: 1; letter-spacing: -1px;
  }

  .headline { font-family: "Montserrat", sans-serif; font-weight: 900; color: var(--shadow-red); line-height: 1; }
  .headline-relish { left: 126px; top: 140px; font-size: 112px; letter-spacing: -3px; }
  .headline-just { left: 558px; top: 148px; font-size: 26px; transform-origin: left top; transform: rotate(90deg) translateY(-26px); letter-spacing: 1px; }
  .headline-got { left: 86px; top: 250px; font-size: 60px; letter-spacing: -3px; }
  .headline-saucy { left: 196px; top: 230px; font-size: 128px; letter-spacing: -4px; }

  .award-seal { left: 248px; top: 340px; width: 220px; height: 170px; }
  .award-label {
    left: 258px; top: 446px; width: 200px; text-align: center;
    font-size: 19px; color: var(--white); font-weight: 400;
  }

  .flavour-banner { left: 178px; top: 497px; width: 356px; height: 60px; }
  .flavour-text {
    left: 178px; top: 512px; width: 356px; text-align: center;
    color: var(--roma-red); font-size: 20px; font-weight: 700; letter-spacing: 0.3px;
  }

  .taste-line { font-size: 20px; font-weight: 600; letter-spacing: 0.5px; line-height: 1; }
  .taste-modern { left: 86px; top: 578px; color: var(--orange); }
  .taste-tradition { right: 82px; top: 600px; color: var(--white); }

  .claim { top: 690px; font-size: 22px; font-weight: 600; letter-spacing: 1.5px; line-height: 1; }
  .claim-gluten { left: 61px; }
  .claim-vegan { right: 45px; }

  .natural-mark { left: 276px; top: 648px; width: 160px; height: 92px; }

  .social-dots { left: 276px; top: 805px; width: 160px; height: 46px; }

  .web-address {
    left: 0; width: 100%; top: 864px; text-align: center;
    font-size: 16px; font-weight: 600; letter-spacing: 1px;
  }
</style>
</head>
<body>
  <main class="shelf-talker">
    <div class="backdrop-burst" role="img" aria-label="Radiating red sunburst rays behind the design"></div>

    <div class="abs brand-name">Corbin &amp; Jules</div>

    <div class="abs headline headline-relish">RELISH</div>
    <div class="abs headline headline-just">JUST</div>
    <div class="abs headline headline-got">GOT</div>
    <div class="abs headline headline-saucy">SAUCY</div>

    <svg class="abs award-seal" viewBox="0 0 220 170" aria-hidden="true">
      <defs>
        <radialGradient id="sealGold" cx="45%" cy="40%" r="65%">
          <stop offset="0" stop-color="#f6dc83"/>
          <stop offset="0.6" stop-color="#e2b54a"/>
          <stop offset="1" stop-color="#b98a1e"/>
        </radialGradient>
      </defs>
      <circle cx="110" cy="82" r="78" fill="url(#sealGold)"/>
      <path d="M6 105 L30 98 L30 128 L6 134 L16 119 Z" fill="#1f5f93"/>
      <path d="M214 105 L190 98 L190 128 L214 134 L204 119 Z" fill="#1f5f93"/>
      <path d="M22 100 Q110 122 198 100 L198 128 Q110 150 22 128 Z" fill="var(--sky-blue)" stroke="#ffffff" stroke-width="1.5"/>
    </svg>
    <div class="abs award-label">award winning</div>

    <svg class="abs flavour-banner" viewBox="0 0 356 60" aria-hidden="true">
      <path d="M0 0 H356 L334 30 L356 60 H0 L22 30 Z" fill="var(--white)"/>
      <path d="M0 60 L22 30 L26 36 Z" fill="#d9d9d9"/>
    </svg>
    <div class="abs flavour-text">LUSCIOUS FULL FLAVOUR</div>

    <div class="abs taste-line taste-modern">MODERN AUSTRALIAN TASTE</div>
    <div class="abs taste-line taste-tradition">.........WITH ECHOES OF TRADITION.</div>

    <div class="abs claim claim-gluten">GLUTEN FREE</div>
    <svg class="abs natural-mark" viewBox="0 0 160 92" aria-label="100% Natural">
      <text x="80" y="48" text-anchor="middle" font-family="Montserrat, sans-serif" font-weight="800" font-size="46" fill="var(--orange)">100%</text>
      <path d="M10 52 H150 L142 64 L150 76 H10 L18 64 Z" fill="var(--orange)"/>
      <text x="80" y="71" text-anchor="middle" font-family="Montserrat, sans-serif" font-weight="800" font-size="15" letter-spacing="2" fill="var(--deep-red)">NATURAL</text>
    </svg>
    <div class="abs claim claim-vegan">VEGAN FRIENDLY</div>

    <svg class="abs social-dots" viewBox="0 0 160 46" aria-hidden="true">
      <circle cx="23" cy="23" r="21" fill="var(--orange)"/>
      <circle cx="80" cy="23" r="21" fill="var(--orange)"/>
      <circle cx="134" cy="23" r="21" fill="var(--orange)"/>
    </svg>

    <div class="abs web-address">WWW.CORBINANDJULES.COM.AU</div>
  </main>
</body>
</html>
```